Velvet Dice Night Age Verification Landing Page

To create a visually appealing design for the landing page of the adult game "Velvet Dice Night" that confirms the visitor's age.
The design should have a simple and visually appealing look that focuses on two buttons labeled "Yes" and "No". The purpose of the page is to confirm that the visitor is 18 years of age or older before accessing the game's content. Responsive design that works well on desktop and mobile devices. The final output should be delivered in PSD, AI, or Sketch format, along with any necessary images or assets.
I have also attached examples.

```html
<!DOCTYPE html>
<html lang="en">
<head>
<meta charset="utf-8">
<title>Velvet Dice Night – Age Verification</title>
<link href="https://fonts.googleapis.com/css2?family=Poppins:wght@400;600;700&display=swap" rel="stylesheet">
<style>
  :root {
    --page-bg: #141414;
    --panel-bg: #0b0b0b;
    --accent: #b05aac;
    --accent-glow: rgba(208, 110, 204, 0.55);
    --text: #ffffff;
  }
  * { margin: 0; padding: 0; box-sizing: border-box; }
  html, body {
    width: 1200px;
    height: 857px;
    overflow: hidden;
    background: var(--page-bg);
    font-family: "Poppins", sans-serif;
    color: var(--text);
  }
  .age-gate {
    position: relative;
    width: 1200px;
    height: 857px;
    overflow: hidden;
  }
  .backdrop-photo {
    position: absolute;
    inset: 0;
    background:
      radial-gradient(ellipse 420px 300px at 420px 360px, #2a2522 0%, rgba(30,27,25,0) 70%),
      radial-gradient(ellipse 380px 420px at 920px 380px, #2b2624 0%, rgba(30,27,25,0) 70%),
      linear-gradient(180deg, #1a1919 0%, #1d1c1c 60%, #161616 100%);
  }
  .brand {
    position: absolute;
    left: 0;
    width: 1200px;
    top: 148px;
    display: flex;
    justify-content: center;
    align-items: center;
    gap: 10px;
  }
  .brand-dot {
    width: 14px;
    height: 14px;
    border-radius: 50%;
    background: var(--accent);
  }
  .brand-name {
    font-weight: 600;
    font-size: 26px;
    color: var(--accent);
    letter-spacing: 0.2px;
  }
  .panel-frame {
    position: absolute;
    left: 0;
    top: 0;
    width: 1200px;
    height: 857px;
  }
  .panel-content {
    position: absolute;
    left: 275px;
    top: 313px;
    width: 651px;
    height: 360px;
    text-align: center;
  }
  .question {
    position: absolute;
    left: 0;
    width: 100%;
    top: 82px;
    font-weight: 600;
    font-size: 31px;
    line-height: 44px;
  }
  .choices {
    position: absolute;
    left: 173px;
    top: 158px;
    display: flex;
    gap: 39px;
  }
  .choice {
    width: 133px;
    height: 56px;
    border-radius: 28px 28px 0 28px;
    font-family: "Poppins", sans-serif;
    font-weight: 600;
    font-size: 22px;
    color: var(--text);
    display: flex;
    align-items: center;
    justify-content: center;
    cursor: pointer;
  }
  .choice-yes {
    background: var(--accent);
    border: 2px solid var(--accent);
  }
  .choice-no {
    background: transparent;
    border: 2px solid var(--text);
  }
  .remember {
    position: absolute;
    left: 255px;
    top: 245px;
    display: flex;
    align-items: center;
    gap: 10px;
    font-size: 15.5px;
    font-weight: 400;
  }
  .remember-dot {
    width: 12px;
    height: 12px;
    border-radius: 50%;
    background: var(--text);
  }
</style>
</head>
<body>
  <main class="age-gate">
    <div class="backdrop-photo" role="img" aria-label="Dimmed background photograph of a person lying on a bed"></div>

    <header class="brand">
      <span class="brand-dot"></span>
      <span class="brand-name">Velvet Dice Night</span>
    </header>

    <svg class="panel-frame" viewBox="0 0 1200 857" aria-hidden="true">
      <defs>
        <filter id="frame-glow" x="-10%" y="-10%" width="120%" height="120%">
          <feGaussianBlur stdDeviation="4" result="blur"/>
          <feMerge><feMergeNode in="blur"/><feMergeNode in="SourceGraphic"/></feMerge>
        </filter>
      </defs>
      <path d="M308 278 L892 304 Q943 306 943 357 L943 652 Q943 703 892 701 L308 681 Q257 679 257 628 L257 329 Q257 276 308 278 Z"
            fill="none" stroke="#b05aac" stroke-width="3" filter="url(#frame-glow)"/>
      <rect x="275" y="313" width="651" height="360" rx="50" fill="#0b0b0b"/>
    </svg>

    <section class="panel-content">
      <h1 class="question">Are You Over 18 Years of age?</h1>
      <div class="choices">
        <button class="choice choice-yes">Yes</button>
        <button class="choice choice-no">No</button>
      </div>
      <label class="remember">
        <span class="remember-dot"></span>
        <span>Remember me</span>
      </label>
    </section>
  </main>
</body>
</html>
```